Fresh, modern, fun business card for pediatric dental practice

Need a business card for fresh, modern, fun pediatric dental practice

Clean look that matches our website's font and colors

We prefer the look of curved corners on business cards

Target Market(s)

parents (mothers) of young children, professionals, mid-high class

Industry/Entity Type

Dental

Contact Information for Business Card

Maplebrook Pediatric Dentistry
482 Quarry Lane
Suite 517
Fernvale, PA 17000
717.555.0193
www.maplebrookkidsdental.example

Mei-Ran Tsai, DMD
Corinne Walbeck, DMD
(we are working on our email address, but we would like that on the card as well)

Font styles to use
Sans Serif

Requirements
Must have
• All info; we would also like to make cards for individual staff members
• colors from our website and color palatte, attatched
• use same font and design as website for branding
Nice to have
• clean, simple card that has a pop of color
• we would like to see a few designs with our tag line "where little grins grow big"
• we are not sure if we want to have it on there or not
• we would like to see a few designs incorporating the ribbon graphic on our website where the word WELCOME is

```html
<!DOCTYPE html>
<html lang="en">
<head>
<meta charset="utf-8">
<title>Maplebrook Pediatric Dentistry – Business Card</title>
<link rel="stylesheet" href="https://fonts.googleapis.com/css2?family=Lato:wght@400;700&display=swap">
<style>
  :root {
    --magenta: #c2268f;
    --magenta-light: #d43ea6;
    --gold: #f2b928;
    --gold-deep: #eca21f;
    --ink: #4a4a4a;
    --paper: #f7f7f7;
    --tagline: #fff3d6;
    --backdrop: #e6e3e7;
  }
  * { box-sizing: border-box; margin: 0; padding: 0; }
  html, body { width: 1200px; height: 900px; overflow: hidden; }
  body {
    background: var(--backdrop);
    font-family: "Lato", sans-serif;
    display: flex;
    flex-direction: column;
    align-items: center;
    justify-content: center;
    gap: 60px;
  }
  .card {
    width: 630px;
    height: 360px;
    border-radius: 22px;
    overflow: hidden;
    position: relative;
    box-shadow: 0 10px 30px rgba(0,0,0,0.14);
  }

  /* Front */
  .card-front {
    background: var(--paper);
    display: flex;
    align-items: center;
    padding: 0 40px;
  }
  .front-brand { width: 240px; display: flex; align-items: center; gap: 12px; flex: none; }
  .brand-dot { width: 22px; height: 22px; border-radius: 50%; background: var(--gold); flex: none; }
  .brand-name {
    color: var(--gold);
    font-weight: 700;
    font-size: 27px;
    line-height: 1.1;
  }
  .divider { width: 2px; height: 190px; background: var(--gold); margin: 0 28px 0 10px; flex: none; }
  .details { color: var(--ink); font-size: 15px; line-height: 1.4; min-width: 0; }
  .doctor { color: var(--magenta); font-weight: 700; font-size: 24px; margin-bottom: 6px; }
  .doctor .degree { color: var(--gold); font-weight: 400; }
  .practice { color: var(--magenta); font-weight: 700; font-size: 15px; }
  .address { margin-bottom: 10px; }
  .contact-row { display: flex; align-items: center; gap: 8px; white-space: nowrap; }
  .contact-row svg { width: 16px; height: 16px; flex: none; }

  /* Back */
  .card-back { background: linear-gradient(160deg, var(--magenta-light), var(--magenta)); }
  .back-band {
    position: absolute; left: 0; right: 0; bottom: 0; height: 118px;
    background: linear-gradient(180deg, var(--gold), var(--gold-deep));
    display: flex; align-items: center; justify-content: center;
  }
  .tagline { color: var(--tagline); font-size: 18px; letter-spacing: 0.5px; }
  .back-brand {
    position: absolute; top: 0; left: 0; right: 0; height: 242px;
    display: flex; align-items: center; justify-content: center; gap: 16px;
  }
  .back-brand .brand-name { font-size: 38px; }
  .back-brand .brand-dot { width: 30px; height: 30px; }
</style>
</head>
<body>
  <section class="card card-front" aria-label="Business card front">
    <div class="front-brand">
      <span class="brand-dot"></span>
      <span class="brand-name">Maplebrook Pediatric Dentistry</span>
    </div>
    <div class="divider"></div>
    <div class="details">
      <p class="doctor">Mei-Ran Tsai, <span class="degree">DMD</span></p>
      <p class="practice">Maplebrook Pediatric Dentistry</p>
      <p class="address">482 Quarry Lane, Suite 517<br>Fernvale, PA 17000</p>
      <p class="contact-row">
        <svg viewBox="0 0 16 16"><circle cx="8" cy="8" r="8" fill="#c2268f"/><path d="M5.2 4.2l1.4-.3.8 1.9-1 .7a6 6 0 0 0 2.9 2.9l.7-1 1.9.8-.3 1.4c-3.6.3-6.7-2.8-6.4-6.4z" fill="#fff"/></svg>
        717.555.0193
      </p>
      <p class="contact-row">
        <svg viewBox="0 0 16 16"><circle cx="8" cy="8" r="8" fill="#c2268f"/><rect x="4" y="5" width="8" height="6" rx="1" fill="#fff"/><path d="M4.3 5.4L8 8.3l3.7-2.9" stroke="#c2268f" stroke-width="1" fill="none"/></svg>
        info@maplebrookkidsdental.example
      </p>
      <p class="contact-row">
        <svg viewBox="0 0 16 16"><circle cx="8" cy="8" r="8" fill="#c2268f"/><circle cx="8" cy="8" r="4" stroke="#fff" stroke-width="1" fill="none"/><ellipse cx="8" cy="8" rx="1.7" ry="4" stroke="#fff" stroke-width="1" fill="none"/><path d="M4 8h8" stroke="#fff" stroke-width="1"/></svg>
        www.maplebrookkidsdental.example
      </p>
    </div>
  </section>

  <section class="card card-back" aria-label="Business card back">
    <div class="back-brand">
      <span class="brand-dot"></span>
      <span class="brand-name">Maplebrook Pediatric Dentistry</span>
    </div>
    <div class="back-band">
      <p class="tagline">where little grins grow big</p>
    </div>
  </section>
</body>
</html>
```